BPW its me again- No TIME

I am a weight loss consultant who my target audience now is staff- teachers at work.

I am Bright Path Wellness and I have partner up with the program Vital Spark Reset. I am selling my services but it will be attached to his brochure which I attached to show you.

This flyer will be given to teachers while at work or left on the staff room lunch table.

Please make it short, snappy and fun.
Why lose weight at work? People are time poor

points:-
- Mobile weight loss consultant who comes to you at work
before/after school or lunch break.
-20 minute private 1 on 1 consultations
-limited spots (3 per hour)
-no contract
-10 years experience

If possible I would like it at work flyer for different companies as well like banks but teachers/schools are my main target.

Like the picture with the teacher in front of the board but can remove the heart if possible
Thank you

i will brochure soon to show you

Target Market(s)

people at work- during lunch breaks or before and after
First is school teachers then other companies.
Females are the majority of clients

Industry/Entity Type

Teacher

Requirements
Must have
• leave it up to you just want to grab staff's attention.
Should not have
• please never use the word "diet" its a healthy lifestyle.

```html
<!DOCTYPE html>
<html lang="en">
<head>
<meta charset="utf-8">
<title>Why lose weight at work? – Bright Path Wellness</title>
<link href="https://fonts.googleapis.com/css2?family=Didact+Gothic&display=swap" rel="stylesheet">
<style>
  :root {
    --title-red: #d6263f;
    --rule-red: #d62a3a;
    --headline-blue: #2c5aa6;
    --leaf-green: #b7d98c;
    --leaf-green-deep: #8cc152;
    --text-green: #2e6a26;
    --purple: #7a3d8e;
    --purple-band: #6f3e8c;
    --point-green: #5e9a2e;
    --point-red: #b3262e;
    --point-blue: #2878ae;
    --grey-light: #eeeeef;
    --grey-mid: #dcdcde;
    --white: #ffffff;
  }
  * { margin: 0; padding: 0; box-sizing: border-box; }
  html, body { width: 851px; height: 1200px; overflow: hidden; background: var(--white); }
  body { font-family: "Didact Gothic", "Century Gothic", sans-serif; }
  .flyer { position: relative; width: 851px; height: 1200px; overflow: hidden; background: var(--white); }
  .backdrop { position: absolute; inset: 0; }
  .flyer-title {
    position: absolute; left: 40px; top: 22px;
    font-size: 42px; font-weight: 400; color: var(--title-red); letter-spacing: 0.3px;
  }
  .headline {
    position: absolute; left: 135px; top: 124px;
    font-size: 50px; font-weight: 400; color: var(--headline-blue);
  }
  .offer {
    position: absolute; left: 28px; top: 248px;
    color: var(--text-green); font-size: 31px; line-height: 46px;
  }
  .offer .role { text-transform: uppercase; letter-spacing: 0.5px; }
  .points { position: absolute; left: 40px; top: 704px; list-style: none; }
  .points li { position: relative; font-size: 27px; height: 62px; line-height: 40px; }
  .points li span { position: relative; }
  .points .swatch {
    position: absolute; left: -8px; top: 4px; width: 150px; height: 34px;
    border-radius: 18px 6px 20px 8px; transform: rotate(-6deg); opacity: 0.75;
  }
  .point-purple { color: var(--purple); }
  .point-purple .swatch { background: #b68fc6; }
  .point-green { color: var(--point-green); }
  .point-green .swatch { background: #c7e2a4; }
  .point-red { color: var(--point-red); }
  .point-red .swatch { background: #efa3a8; }
  .point-blue { color: var(--point-blue); }
  .point-blue .swatch { background: #a6d3ee; }
  .brand {
    position: absolute; left: 470px; top: 975px;
    display: flex; align-items: center; gap: 12px;
  }
  .brand-dot { width: 30px; height: 30px; border-radius: 50%; background: var(--purple); }
  .brand-name { font-size: 30px; color: var(--purple); }
  .contact-band {
    position: absolute; left: 0; top: 1097px; width: 851px; height: 103px;
    background: var(--purple-band); color: var(--white);
    font-size: 21px; letter-spacing: 0.4px;
  }
  .contact-row { position: absolute; left: 0; width: 851px; text-align: center; }
  .contact-row.first { top: 13px; }
  .contact-row.second { top: 51px; }
  .sep { margin: 0 14px; }
</style>
</head>
<body>
<main class="flyer">
  <svg class="backdrop" width="851" height="1200" viewBox="0 0 851 1200">
    <defs>
      <linearGradient id="topFade" x1="0" y1="0" x2="0" y2="1">
        <stop offset="0" stop-color="#ffffff"/>
        <stop offset="1" stop-color="#ececec"/>
      </linearGradient>
      <linearGradient id="lowerGrey" x1="0" y1="0" x2="1" y2="1">
        <stop offset="0" stop-color="#e4e4e6"/>
        <stop offset="1" stop-color="#f4f4f5"/>
      </linearGradient>
      <linearGradient id="photoTone" x1="0" y1="0" x2="1" y2="1">
        <stop offset="0" stop-color="#f4f1ee"/>
        <stop offset="0.5" stop-color="#7aa04a"/>
        <stop offset="1" stop-color="#e6dccb"/>
      </linearGradient>
      <linearGradient id="propTone" x1="0" y1="0" x2="1" y2="1">
        <stop offset="0" stop-color="#d23a6a"/>
        <stop offset="0.6" stop-color="#9cc94a"/>
        <stop offset="1" stop-color="#f1f1f1"/>
      </linearGradient>
    </defs>
    <!-- header band -->
    <rect x="0" y="0" width="851" height="92" fill="url(#topFade)"/>
    <rect class="rule" x="0" y="91" width="851" height="6" fill="var(--rule-red)"/>
    <rect x="0" y="97" width="851" height="3" fill="#c9c9c9"/>
    <!-- green wedge -->
    <polygon points="0,100 742,100 0,608" fill="var(--leaf-green)"/>
    <!-- teacher photo area -->
    <polygon role="img" aria-label="Smiling teacher in a green cardigan leaning on a stack of books with a laptop and an apple"
      points="305,255 851,255 851,728 305,652" fill="url(#photoTone)"/>
    <!-- lower grey area with green diagonal -->
    <polygon points="0,610 851,733 851,1097 0,1097" fill="url(#lowerGrey)"/>
    <polygon points="330,1097 851,860 851,1097" fill="#fafafa"/>
    <polygon points="0,604 851,727 851,736 0,614" fill="var(--leaf-green-deep)"/>
    <!-- small props photo -->
    <polygon role="img" aria-label="Pink dumbbells, a green apple and a tape measure"
      points="0,955 360,955 400,1097 0,1097" fill="#f2f2f2"/>
    <rect role="img" aria-label="Pink dumbbells, a green apple and a tape measure"
      x="25" y="965" width="160" height="128" rx="10" fill="url(#propTone)"/>
    <!-- partner badge -->
    <rect role="img" aria-label="Vital Spark Reset official partner badge"
      x="237" y="982" width="124" height="86" rx="8" fill="#ffffff" stroke="#d62a3a" stroke-width="3"/>
    <!-- brand paint backdrop -->
    <rect role="img" aria-label="Colourful paint strokes behind the brand name"
      x="450" y="890" width="390" height="140" rx="40" fill="#e9e3ef"/>
  </svg>

  <h1 class="flyer-title">Why lose weight at work?</h1>
  <h2 class="headline">People are time poor</h2>

  <p class="offer">
    Mobile<br>
    <span class="role">Weight loss consultant</span><br>
    who comes to you at work<br>
    before/after school<br>
    or lunch break.
  </p>

  <ul class="points">
    <li class="point-purple"><i class="swatch"></i><span>20 minute private 1 on 1 consultations</span></li>
    <li class="point-green"><i class="swatch"></i><span>Limited spots (3 per hour)</span></li>
    <li class="point-red"><i class="swatch"></i><span>No contract</span></li>
    <li class="point-blue"><i class="swatch"></i><span>10 years experience</span></li>
  </ul>

  <div class="brand">
    <span class="brand-dot"></span>
    <span class="brand-name">Bright Path Wellness</span>
  </div>

  <footer class="contact-band">
    <div class="contact-row first">+61 400 555 018<span class="sep">|</span>hello@brightpathwellness.com.au</div>
    <div class="contact-row second">www.brightpathwellness.com.au<span class="sep">|</span>Maple Grove, Victoria, Australia 3999</div>
  </footer>
</main>
</body>
</html>
```